Strategic design partner needed for newly global technical consultancy! Starting with PowerPoint!

Quillbrook.biz is a new consulting company offering technical assurance (reliability, business and cyber resiliency, operational excellence, and technical agility). We already have a logo (attached) and main font (Montserrat). Our colour scheme is gold and charcoal (color code of charcoal is #36454F, and for the gold is #B69904).
See the attachment for full colour palette we want! We need to partner with a designer for our corporate branding, starting with a PowerPoint deck that will be used for proposals and client meetings.
In a proposal deck we have items like Problem Statement (our joint understanding), Our Approach, Architecture, Timeline, Team, Assumptions/Dependencies/Risks, RACI, Pricing.
For corporate presentations we would have Introduction, Services, Methodology, Case Studies, Team, Clients, Contact.
This could lead to much more work. The website is just a placeholder, but we like the colours (quillbrook dot biz)

Industry/Entity Type

Technology solutions apply across all industries. We have clients in fintech, pharma, retail, etc.

Requirements
Must have
• Match the colour scheme - SEE UPLOADED ATTACHMENT

```html
<!DOCTYPE html>
<html lang="en">
<head>
<meta charset="utf-8">
<title>Quillbrook – Presentation Deck Overview</title>
<link href="https://fonts.googleapis.com/css2?family=Roboto:wght@300;400;500;700;900&display=swap" rel="stylesheet">
<style>
:root{
  --gold:#c4922f;
  --gold-dark:#a8782a;
  --olive:#a89a3a;
  --brown:#7a5a45;
  --charcoal:#1f262e;
  --charcoal-2:#2a323b;
  --ink:#222;
  --grey:#8a8a8a;
  --line:#d9d9d9;
  --canvas:#c9c9c9;
}
*{box-sizing:border-box;margin:0;padding:0}
html,body{width:1200px;height:1053px;overflow:hidden;background:var(--canvas);font-family:'Roboto',sans-serif;color:var(--ink)}
.deck{position:relative;width:1200px;height:1053px}
.slide{position:absolute;width:277px;height:156px;background:#fff;overflow:hidden;box-shadow:0 1px 3px rgba(0,0,0,.18)}
.c1{left:16px}.c2{left:313px}.c3{left:610px}.c4{left:907px}
.r1{top:13px}.r2{top:186px}.r3{top:359px}.r4{top:532px}.r5{top:704px}.r6{top:877px}
.abs{position:absolute}
.photo{position:absolute}
.flag{position:absolute;left:12px;top:0;width:14px;height:7px}
.title{position:absolute;left:12px;top:11px;font-size:9px;font-weight:700;color:var(--ink);letter-spacing:-.1px;white-space:nowrap}
.title b,.gold{color:var(--gold);font-weight:700}
.sub{position:absolute;left:12px;top:23px;font-size:3px;color:var(--grey)}
.t{font-size:3px;line-height:1.4;color:var(--grey)}
.tw{font-size:3px;line-height:1.4;color:#d0d0d0}
.h{font-weight:700;color:var(--ink)}
.foot{position:absolute;right:8px;bottom:5px;display:flex;height:4px}
.foot span{background:var(--charcoal);color:#fff;font-size:2px;width:44px;display:flex;align-items:center;justify-content:center}
.foot i{background:var(--gold);width:6px;color:#fff;font-size:2px;font-style:normal;display:flex;align-items:center;justify-content:center}
.mark{display:inline-block;width:9px;height:9px;background:var(--gold)}
.center{text-align:center}
.box{position:absolute;display:flex;flex-direction:column;align-items:center;justify-content:center;color:#fff}
table{border-collapse:collapse}
.tbl td,.tbl th{font-size:2.6px;height:5.1px;text-align:center;color:#777;font-weight:400}
.client{font-size:7px;color:var(--ink);font-weight:500}
</style>
</head>
<body>
<div class="deck">

<!-- 1 cover -->
<section class="slide c1 r1" style="background:var(--charcoal)">
  <div class="photo" role="img" aria-label="Hand holding a small green padlock" style="inset:0;background:linear-gradient(100deg,#1f262e 0%,#222a32 45%,#3b4148 70%,#555a5e 100%)"></div>
  <div class="abs" style="left:8px;top:0;width:1.5px;height:156px;background:var(--gold)"></div>
  <div class="abs" style="left:40px;top:44px"><span class="mark"></span></div>
  <div class="abs" style="left:37px;top:64px;font-size:13px;font-weight:700;color:#fff">Quillbrook</div>
  <div class="abs" style="left:37px;top:82px;font-size:5.5px;color:var(--gold)">Assuring Your Advantage</div>
  <p class="abs" style="left:37px;top:95px;width:150px;font-size:4.2px;line-height:1.4;color:#cfd2d5">We are new consulting company offering technical assurance (reliability, business and cyber resiliency, operational excellence, and technical agility)</p>
  <div class="abs" style="left:37px;top:124px;width:150px;height:.3px;background:#555"></div>
  <div class="abs" style="left:37px;top:128px;display:flex;gap:18px;font-size:2.3px;color:#ccc">
    <span>info@quillbrook.biz</span><span>+(351)555-01-47</span><span>Lisbon, Oslo, Perth</span>
  </div>
</section>

<!-- 2 about -->
<section class="slide c2 r1">
  <div class="photo" role="img" aria-label="Office desk with monitor showing a protection sign" style="inset:0;background:linear-gradient(120deg,#c8d0d2,#8c9598 40%,#2c2f33 80%)"></div>
  <svg class="abs" style="left:0;top:0" width="277" height="156"><polygon points="0,60 94,8 277,148 277,156 0,156" fill="#fff"/></svg>
  <div class="abs" style="left:89px;top:57px"><span class="mark"></span></div>
  <div class="abs center" style="left:40px;top:84px;width:110px;font-size:8px;font-weight:700">About <span class="gold">Our Company</span></div>
  <div class="abs center t" style="left:40px;top:96px;width:110px">Insert Your Creative Idea</div>
  <p class="abs center t" style="left:45px;top:108px;width:100px;font-size:2.6px">Lorem ipsum dolor sit amet consectetur adipiscing elit nulla imperdiet volutpat dui at fermentum aliquam erat volutpat aenean lacinia aliquet ante mollis</p>
</section>

<!-- 3 welcome -->
<section class="slide c3 r1">
  <div class="photo" role="img" aria-label="Portrait of a smiling man in a suit" style="left:12px;top:0;width:60px;height:50px;background:linear-gradient(180deg,#d4d7da,#6d7378)"></div>
  <div class="photo" role="img" aria-label="Business people discussing documents at a table" style="left:93px;top:0;width:184px;height:156px;background:linear-gradient(110deg,#e6e4df,#c9c3b8 50%,#9a9185)"></div>
  <div class="abs" style="left:12px;top:57px;font-size:8px;font-weight:700">WELCOME</div>
  <div class="abs" style="left:12px;top:66px;font-size:8px;font-weight:300;color:var(--gold);letter-spacing:.3px">MESSAGE</div>
  <div class="abs" style="left:12px;top:77px;width:70px;height:.5px;background:#444"></div>
  <div class="abs t" style="left:12px;top:81px">Insert Your Creative Idea</div>
  <p class="abs t" style="left:12px;top:89px;width:58px;font-size:2.6px;text-align:justify"><b class="h">Lorem ipsum</b> dolor sit amet consectetur adipiscing elit nulla imperdiet volutpat dui at fermentum aliquam erat volutpat aenean lacinia lacus aliquet ante mollis tempor tortor aliquam</p>
  <div class="abs" style="left:94px;top:110px;width:82px;height:28px;background:rgba(40,44,48,.92);padding:4px 4px">
    <div style="font-size:6.5px;font-weight:500;color:#fff">YES ! GO AHEAD</div>
    <div class="tw" style="font-size:2.3px">Lorem ipsum dolor sit amet, consectetur adipiscing elit nulla imperdiet volutpat dui</div>
  </div>
</section>

<!-- 4 featured -->
<section class="slide c4 r1">
  <svg class="flag" viewBox="0 0 14 7"><polygon points="0,0 13,0 13,7 6,3" fill="var(--gold)"/><polygon points="0,0 6,3 3,4" fill="var(--charcoal)"/></svg>
  <div class="title">Company <b>Featured</b></div>
  <div class="sub">Insert Your Creative Idea</div>
  <svg class="abs" style="left:0;top:54px" width="277" height="22" fill="none" stroke="#333" stroke-width=".8">
    <circle cx="52" cy="6" r="3.8"/><path d="M50 11h4M50.5 12.8h3"/>
    <path d="M132 8 145 1 140 13 137 9z M137 9 145 1"/>
    <path d="M216 0v14M220 0v14M224 0v14"/><circle cx="216" cy="5" r="1.3"/><circle cx="220" cy="9" r="1.3"/><circle cx="224" cy="4" r="1.3"/>
    <path d="M37 19h30M122 19h30" stroke-width=".9"/>
    <path d="M208 19h30" stroke="var(--gold)" stroke-width=".9"/>
  </svg>
  <div class="abs" style="left:0;top:81px;width:277px;display:flex;justify-content:space-around;padding:0 13px">
    <div class="center" style="width:60px"><div style="font-size:4.3px;font-weight:700">OUR VISION</div><p class="t" style="margin-top:5px">Lorem ipsum dolor sit amet consectetur adipiscing elit nulla imperdiet volutpat dui at fermentum.</p></div>
    <div class="center" style="width:60px"><div style="font-size:4.3px;font-weight:700">OUR MISSION</div><p class="t" style="margin-top:5px">Lorem ipsum dolor sit amet consectetur adipiscing elit nulla imperdiet volutpat dui at fermentum.</p></div>
    <div class="center" style="width:60px"><div style="font-size:4.3px;font-weight:700">OUR RESULT</div><p class="t" style="margin-top:5px">Lorem ipsum dolor sit amet consectetur adipiscing elit nulla imperdiet volutpat dui at fermentum.</p></div>
  </div>
  <div class="foot"><span>www.quillbrook.biz</span><i>4</i></div>
</section>

<!-- 5 approach -->
<section class="slide c1 r2">
  <div class="abs" style="left:159px;top:13px"><span class="mark"></span></div>
  <div class="abs" style="right:103px;top:32px;font-size:8.5px;font-weight:700">Company <span class="gold">Approach</span></div>
  <div class="abs t" style="right:103px;top:43px">Insert Your Creative Idea</div>
  <div class="box" style="left:21px;top:64px;width:46px;height:30px;background:var(--charcoal)"><b style="font-size:7px">15K</b><span style="font-size:3px;text-align:center;margin-top:2px">LOREM IPSUM<br>DOLOR</span></div>
  <div class="box" style="left:72px;top:64px;width:46px;height:30px;background:var(--gold)"><b style="font-size:7px">455K</b><span style="font-size:3px;text-align:center;margin-top:2px">LOREM IPSUM<br>DOLOR</span></div>
  <div class="box" style="left:123px;top:64px;width:46px;height:30px;background:var(--olive)"><b style="font-size:7px">6455K</b><span style="font-size:3px;text-align:center;margin-top:2px">LOREM IPSUM<br>DOLOR</span></div>
  <p class="abs t" style="left:22px;top:99px;width:44px;font-size:2.5px">Lorem ipsum dolor sit amet consectetur adipiscing elit nulla imperdiet dui at fermentum aliquam erat volutpat.</p>
  <p class="abs t" style="left:73px;top:99px;width:44px;font-size:2.5px">Lorem ipsum dolor sit amet consectetur adipiscing elit nulla imperdiet dui at fermentum aliquam erat volutpat.</p>
  <p class="abs t" style="left:124px;top:99px;width:44px;font-size:2.5px">Lorem ipsum dolor sit amet consectetur adipiscing elit nulla imperdiet dui at fermentum aliquam erat volutpat.</p>
  <div class="photo" role="img" aria-label="Hands typing on a laptop keyboard with a standard overlay" style="left:184px;top:0;width:76px;height:85px;background:linear-gradient(160deg,#b9c4cc,#5d6a74 60%,#2b3238)"></div>
  <div class="abs" style="left:184px;top:85px;width:76px;height:59px;background:var(--charcoal);padding:8px 8px">
    <div style="display:flex;align-items:center;gap:4px;color:#fff">
      <svg width="10" height="8" fill="none" stroke="#fff" stroke-width=".7"><rect x=".5" y="1.8" width="9" height="5.7" rx="1"/><circle cx="5" cy="4.6" r="1.7"/></svg>
      <div><b style="font-size:5px">158000+</b><div style="font-size:4px">Photography</div></div>
    </div>
    <div style="height:.3px;background:#555;margin:6px 0 4px"></div>
    <p class="tw" style="font-size:2.5px">Lorem ipsum dolor sit amet consectetur adipiscing elit nulla imperdiet volutpat dui at fermentum.</p>
  </div>
</section>

<!-- 6 iconic list -->
<section class="slide c2 r2">
  <svg class="flag" viewBox="0 0 14 7"><polygon points="0,0 13,0 13,7 6,3" fill="var(--gold)"/><polygon points="0,0 6,3 3,4" fill="var(--charcoal)"/></svg>
  <div class="title">Iconic <b>List</b></div>
  <div class="sub">Insert Your Creative Idea</div>
  <div class="abs center" style="left:0;top:37px;width:277px;font-size:5.5px">Our Best <b>Service</b></div>
  <p class="abs center t" style="left:35px;top:45px;width:207px;font-size:2.5px">Lorem ipsum dolor sit amet consectetur adipiscing elit nulla imperdiet volutpat dui at fermentum aliquam erat volutpat aenean lacinia lacus aliquet ante mollis</p>
  <svg class="abs" style="left:0;top:70px" width="277" height="50" fill="var(--charcoal)">
    <path d="M13 7 18 3 23 7v4h-3v-3h-4v3h-3z"/>
    <path d="M104 1a5 5 0 1 0 5 5h-5z"/><path d="M105.5 0a5 5 0 0 1 4.5 4.5h-4.5z" fill="var(--gold)"/>
    <path d="M191 3h9v6h-9z M191 3l4.5 3 4.5-3" fill="none" stroke="var(--charcoal)" stroke-width=".8"/>
    <path d="M14 41h1.5v8H14zM17 41h1.5v8H17zM20 41h1.5v8H20z"/>
    <rect x="103" y="41" width="10" height="5"/><rect x="105" y="38" width="6" height="3" fill="#999"/><rect x="105" y="46" width="6" height="3" fill="#999"/>
    <path d="M192 40h8v5h-3l-2 2v-2h-3z"/>
  </svg>
  <div class="abs" style="left:30px;top:69px;width:240px;display:grid;grid-template-columns:repeat(3,1fr);row-gap:18px;column-gap:12px">
    <div><div style="font-size:3px;font-weight:700;letter-spacing:.5px">TARGET</div><p class="t" style="font-size:2.4px">It's using to make Your look good and awesome in Your Audiences view. We think with this You well be the best.</p></div>
    <div><div style="font-size:3px;font-weight:700;letter-spacing:.5px">STRATEGY</div><p class="t" style="font-size:2.4px">It's using to make Your look good and awesome in Your Audiences view. We think with this You well be the best.</p></div>
    <div><div style="font-size:3px;font-weight:700;letter-spacing:.5px">RESULT</div><p class="t" style="font-size:2.4px">It's using to make Your look good and awesome in Your Audiences view. We think with this You well be the best.</p></div>
    <div><div style="font-size:3px;font-weight:700;letter-spacing:.5px">CAMPAIGN</div><p class="t" style="font-size:2.4px">It's using to make Your look good and awesome in Your Audiences view. We think with this You well be the best.</p></div>
    <div><div style="font-size:3px;font-weight:700;letter-spacing:.5px">ANALYZE</div><p class="t" style="font-size:2.4px">It's using to make Your look good and awesome in Your Audiences view. We think with this You well be the best.</p></div>
    <div><div style="font-size:3px;font-weight:700;letter-spacing:.5px">OPTIMIZE</div><p class="t" style="font-size:2.4px">It's using to make Your look good and awesome in Your Audiences view. We think with this You well be the best.</p></div>
  </div>
  <div class="foot"><span>www.quillbrook.biz</span><i>6</i></div>
</section>

<!-- 7 timeline -->
<section class="slide c3 r2">
  <svg class="flag" viewBox="0 0 14 7"><polygon points="0,0 13,0 13,7 6,3" fill="var(--gold)"/><polygon points="0,0 6,3 3,4" fill="var(--charcoal)"/></svg>
  <div class="title">Our <b>Timeline</b></div>
  <div class="sub">Insert Your Creative Idea</div>
  <div class="abs center" style="left:0;top:39px;width:277px;font-size:5.5px">Our Best <b>Timeline</b></div>
  <p class="abs center t" style="left:35px;top:47px;width:207px;font-size:2.5px">Lorem ipsum dolor sit amet consectetur adipiscing elit nulla imperdiet volutpat dui at fermentum aliquam erat volutpat aenean lacinia lacus aliquet</p>
  <svg class="abs" style="left:0;top:62px" width="277" height="30">
    <line x1="24" y1="8.5" x2="253" y2="8.5" stroke="#ccc" stroke-width=".8"/>
    <g font-size="3" font-weight="700" text-anchor="middle" fill="#fff">
      <circle cx="43" cy="8.5" r="3.5" fill="#1f262e"/><text x="43" y="9.6">1</text>
      <circle cx="82" cy="8.5" r="3.5" fill="#2c3036"/><text x="82" y="9.6">2</text>
      <circle cx="120" cy="8.5" r="3.5" fill="#6b4e2c"/><text x="120" y="9.6">3</text>
      <circle cx="159" cy="8.5" r="3.5" fill="#a8782a"/><text x="159" y="9.6">4</text>
      <circle cx="197" cy="8.5" r="3.5" fill="#d1a33a"/><text x="197" y="9.6">5</text>
      <circle cx="236" cy="8.5" r="3.5" fill="#e8c55a"/><text x="236" y="9.6">6</text>
    </g>
    <g fill="none" stroke="#333" stroke-width=".8">
      <rect x="39" y="20" width="8" height="6" rx="1"/><rect x="78" y="20" width="8" height="6"/><rect x="118" y="19" width="4.5" height="8" rx=".8" stroke="var(--gold)"/>
      <path d="M156 27l3-7 3 7" stroke="var(--gold)"/><rect x="193" y="20" width="8" height="6" stroke="var(--gold)"/><rect x="232" y="20" width="8" height="6" stroke="#e8c55a"/>
    </g>
  </svg>
  <div class="abs" style="left:27px;top:100px;width:232px;display:grid;grid-template-columns:repeat(6,1fr);column-gap:4px">
    <div class="center"><div style="font-size:2.7px;font-weight:700">SOCIAL MEDIA MARKETING</div><p class="t" style="font-size:2.2px;margin-top:2px">It's using to make Your look good and awesome in Your Audiences view.</p></div>
    <div class="center"><div style="font-size:2.7px;font-weight:700">WEB MARKETING</div><p class="t" style="font-size:2.2px;margin-top:2px">It's using to make Your look good and awesome in Your Audiences view.</p></div>
    <div class="center"><div style="font-size:2.7px;font-weight:700">MOBILE MARKETING</div><p class="t" style="font-size:2.2px;margin-top:2px">It's using to make Your look good and awesome in Your Audiences view.</p></div>
    <div class="center"><div style="font-size:2.7px;font-weight:700">AFFILIATE MARKETING</div><p class="t" style="font-size:2.2px;margin-top:2px">It's using to make Your look good and awesome in Your Audiences view.</p></div>
    <div class="center"><div style="font-size:2.7px;font-weight:700">VIDEO MARKETING</div><p class="t" style="font-size:2.2px;margin-top:2px">It's using to make Your look good and awesome in Your Audiences view.</p></div>
    <div class="center"><div style="font-size:2.7px;font-weight:700">EMAIL MARKETING</div><p class="t" style="font-size:2.2px;margin-top:2px">It's using to make Your look good and awesome in Your Audiences view.</p></div>
  </div>
  <div class="foot"><span>www.quillbrook.biz</span><i>7</i></div>
</section>

<!-- 8 life style -->
<section class="slide c4 r2" style="background:#e7e9ee">
  <div class="photo" role="img" aria-label="Close-up of a blue eye with a digital interface overlay" style="inset:0;clip-path:polygon(105px 0,277px 0,277px 156px,30px 156px);background:radial-gradient(circle at 175px 95px,#5a7690 0,#2a3440 22px,#9aa3ad 60px,#d0d4d9 120px)"></div>
  <div class="abs" style="left:20px;top:72px;width:123px;height:44px;background:var(--charcoal);display:flex;align-items:center;padding:0 6px;gap:6px">
    <span class="mark" style="flex:none;width:10px;height:10px"></span>
    <div>
      <div style="font-size:7px;font-weight:700;color:#fff">LIFE <span class="gold">STYLE</span></div>
      <p class="tw" style="font-size:2.4px;margin-top:2px">Lorem ipsum dolor sit amet consectetur adipiscing elit nulla imperdiet volutpat dui at fermentum aliquam erat volutpat aenean lacinia lacus aliquet ante mollis tempor tortor aliquam nulla facilisi.</p>
    </div>
  </div>
</section>

<!-- 9 meet concept -->
<section class="slide c1 r3">
  <div class="photo" role="img" aria-label="Close-up of a blue eye" style="left:0;top:0;width:84px;height:87px;background:radial-gradient(circle at 45px 45px,#3d6e92 0,#223444 14px,#6b7278 30px,#b7bbbf 60px)"></div>
  <div class="photo" role="img" aria-label="Woman in red jacket working at a computer in an office" style="left:84px;top:87px;width:193px;height:69px;background:linear-gradient(90deg,#2a2f34,#6d7379 40%,#b0412f 62%,#d8d8d6 80%,#efefed)"></div>
  <div class="abs" style="left:92px;top:92px;font-size:7px;font-weight:700;color:#fff;line-height:1.1;opacity:.9">LIFE IS<br>VERY<br>INTERE<br>STING</div>
  <div class="abs" style="left:92px;top:13px;font-size:3.6px;font-weight:700">MARA DELL</div>
  <div class="abs" style="left:92px;top:19px;width:38px;height:3px;background:var(--charcoal);font-size:1.8px;color:#fff;padding-left:2px">CEO</div>
  <p class="abs t" style="left:92px;top:29px;width:62px;font-size:2.4px;text-align:justify">Nulla facilisi nam auctor metus vitae quam gravida ac vehicula elit mollis nunc elementum fringilla nisl a ornare arcu condimentum a nulla euismod congue arcu quis feugiat phasellus porttitor felis mauris vitae quam gravida ac vehicula elit mollis nunc elementum</p>
  <svg class="abs" style="left:166px;top:30px" width="32" height="32"><circle cx="16" cy="16" r="13" fill="none" stroke="#eee" stroke-width="1.2"/><circle cx="16" cy="16" r="13" fill="none" stroke="var(--gold)" stroke-width="1.2" stroke-dasharray="69 82" transform="rotate(-90 16 16)"/><text x="16" y="17" font-size="4.5" font-weight="700" text-anchor="middle">85%</text><text x="16" y="20.5" font-size="1.8" text-anchor="middle" fill="#888">DESIGN</text></svg>
  <div class="abs" style="left:203px;top:31px;font-size:3.4px;font-weight:700">TARGET</div>
  <div class="abs" style="left:203px;top:37px;font-size:2.5px;font-weight:700;line-height:1.2">CEO, Founder<br>BEST PRODUCT</div>
  <p class="abs t" style="left:203px;top:44px;width:40px;font-size:2.3px">It's using to make Your look good and awesome in Your Audiences view.</p>
  <div class="abs" style="left:9px;top:96px;font-size:8px;font-weight:700;line-height:1.15">Meet<br>Awesome<br><span class="gold">Concept</span></div>
  <div class="abs t" style="left:9px;top:131px">Insert Your Creative Idea</div>
</section>

<!-- 10 key study -->
<section class="slide c2 r3" style="background:#efefef">
  <div class="photo" role="img" aria-label="Golden-toned close-up of an eye with a tech overlay" style="left:13px;top:29px;width:186px;height:103px;background:radial-gradient(circle at 100px 48px,#8b7340 0,#3a3526 30px,#1c1f22 80px)"></div>
  <div class="abs" style="left:18px;top:46px;font-size:7.5px;font-weight:700;color:#fff;line-height:1.2">It's The<br>Best Of <span class="gold">Key</span><br><span class="gold">Study</span> 2023</div>
  <p class="abs tw" style="left:18px;top:81px;width:55px;font-size:2.5px">Nulla imperdiet volutpat dui at fermentum. Aliquam erat volutpat. Aenean lacinia</p>
  <div class="abs" style="left:202px;top:29px;width:62px;height:103px;background:var(--charcoal-2);padding:15px 0 0 13px;color:#ccc;font-size:2.8px;line-height:1.25">
    <div>SHOTTED :</div><div style="font-size:4.5px;color:#fff">25 Oct. 2015</div>
    <div style="margin-top:5px">SNAPAT :</div><div style="font-size:4.5px;color:#fff">Place Name</div>
    <div style="margin-top:5px">SHOTTED BY:</div><div style="font-size:4.5px;color:#fff">Jon Dale</div>
    <div style="margin-top:5px;font-size:4.5px">ABOUT :</div><div style="font-size:2.5px;width:40px">Lorem ipsum dolor sit amet nisl modo agam facer time.</div>
  </div>
</section>

<!-- 11 solutions -->
<section class="slide c3 r3">
  <svg class="flag" viewBox="0 0 14 7"><polygon points="0,0 13,0 13,7 6,3" fill="var(--gold)"/><polygon points="0,0 6,3 3,4" fill="var(--charcoal)"/></svg>
  <div class="title">Meet Awesome <b>Solutions</b></div>
  <div class="sub">Insert Your Creative Idea</div>
  <div class="abs" style="left:0;top:37px;width:277px;height:101px;background:#111"></div>
  <div class="photo" role="img" aria-label="Modern office desk with computer monitors" style="left:0;top:37px;width:150px;height:101px;background:linear-gradient(90deg,#b8bcbf,#6f757a 45%,rgba(17,17,17,1))"></div>
  <div class="abs" style="left:66px;top:52px;width:60px;text-align:right;font-size:6.5px;font-weight:700;color:#fff;line-height:1.15">LOREM<br>IPSUM DOLOR</div>
  <p class="abs tw" style="left:131px;top:52px;width:130px;font-size:2.9px">Join with Us and we'll make the world in Our Hand. It's using to make Your look good and awesome in Your Audiences view. We think with this You well be the best. It's using to make Your look good and awesome in Your Audiences view. Believe it!</p>
  <div class="abs" style="left:131px;top:80px;width:130px;display:grid;grid-template-columns:1fr 1fr;row-gap:9px">
    <div style="display:flex;gap:4px"><span style="width:14px;height:14px;border:.5px solid #666;flex:none"></span><div><div style="font-size:3px;color:var(--gold)">Join Now</div><div class="tw" style="font-size:2.2px">We think with this You we'll be the best.</div></div></div>
    <div style="display:flex;gap:4px"><span style="width:14px;height:14px;border:.5px solid #666;flex:none"></span><div><div style="font-size:3px;color:var(--gold)">Join Now</div><div class="tw" style="font-size:2.2px">We think with this You we'll be the best.</div></div></div>
    <div style="display:flex;gap:4px"><span style="width:14px;height:14px;border:.5px solid #666;flex:none"></span><div><div style="font-size:3px;color:var(--gold)">Join Now</div><div class="tw" style="font-size:2.2px">We think with this You we'll be the best.</div></div></div>
    <div style="display:flex;gap:4px"><span style="width:14px;height:14px;border:.5px solid #666;flex:none"></span><div><div style="font-size:3px;color:var(--gold)">Join Now</div><div class="tw" style="font-size:2.2px">We think with this You we'll be the best.</div></div></div>
  </div>
  <div class="foot"><span>www.quillbrook.biz</span><i>11</i></div>
</section>

<!-- 12 prices -->
<section class="slide c4 r3">
  <svg class="flag" viewBox="0 0 14 7"><polygon points="0,0 13,0 13,7 6,3" fill="var(--gold)"/><polygon points="0,0 6,3 3,4" fill="var(--charcoal)"/></svg>
  <div class="title">Our <b>Prices</b></div>
  <div class="sub">Insert Your Creative Idea</div>
  <div class="abs" style="left:23px;top:45px;width:231px;display:grid;grid-template-columns:repeat(4,1fr);gap:1.5px">
    <div style="border:.5px solid #aaa;height:85px;padding:3px"><div class="center" style="font-size:4px">STARTER</div><div class="center" style="background:var(--charcoal);color:#fff;font-size:5.5px;margin-top:2px;padding:1px">$10 <small style="font-size:2px">/Month</small></div><div class="t center" style="font-size:2.2px;line-height:5.5;opacity:.8">5 USERS<br>10 PROJECTS<br>10 GB SPACE MEMORY<br>5 EMAIL ACCOUNT</div></div>
    <div style="border:.5px solid #aaa;height:85px;padding:3px"><div class="center" style="font-size:4px">BASIC</div><div class="center" style="background:var(--brown);color:#fff;font-size:5.5px;margin-top:2px;padding:1px">$20 <small style="font-size:2px">/Month</small></div><div class="t center" style="font-size:2.2px;line-height:5.5;opacity:.8">5 USERS<br>10 PROJECTS<br>10 GB SPACE MEMORY<br>5 EMAIL ACCOUNT</div></div>
    <div style="border:.5px solid #aaa;height:85px;padding:3px"><div class="center" style="font-size:4px">PROFESIONAL</div><div class="center" style="background:var(--gold-dark);color:#fff;font-size:5.5px;margin-top:2px;padding:1px">$30 <small style="font-size:2px">/Month</small></div><div class="t center" style="font-size:2.2px;line-height:5.5;opacity:.8">5 USERS<br>10 PROJECTS<br>10 GB SPACE MEMORY<br>5 EMAIL ACCOUNT</div></div>
    <div style="border:.5px solid #aaa;height:85px;padding:3px"><div class="center" style="font-size:4px">ULTIMATE</div><div class="center" style="background:#d9a53a;color:#fff;font-size:5.5px;margin-top:2px;padding:1px">$40 <small style="font-size:2px">/Month</small></div><div class="t center" style="font-size:2.2px;line-height:5.5;opacity:.8">5 USERS<br>10 PROJECTS<br>10 GB SPACE MEMORY<br>5 EMAIL ACCOUNT</div></div>
  </div>
  <div class="foot"><span>www.quillbrook.biz</span><i>12</i></div>
</section>

<!-- 13 our table -->
<section class="slide c1 r4">
  <svg class="flag" viewBox="0 0 14 7"><polygon points="0,0 13,0 13,7 6,3" fill="var(--gold)"/><polygon points="0,0 6,3 3,4" fill="var(--charcoal)"/></svg>
  <div class="title">Our <b>Table</b></div>
  <div class="sub">Insert Your Creative Idea</div>
  <table class="tbl abs" style="left:12px;top:36px;width:258px">
    <tr><th style="width:111px"></th><th style="background:var(--charcoal);color:#fff;height:6px">DESCRIPTION 01</th><th style="background:var(--brown);color:#fff">DESCRIPTION 02</th><th style="background:var(--gold);color:#fff">DESCRIPTION 03</th></tr>
    <tr style="background:#d8d8d8"><td>Description and Text Goes here</td><td>80.098</td><td>80.873</td><td>76.9838</td></tr>
    <tr style="background:#eee"><td>Description and Text Goes here</td><td>20.09</td><td>20.09</td><td>20.09</td></tr>
    <tr style="background:#d8d8d8"><td>Description and Text Goes here</td><td>20.09</td><td>20.09</td><td>20.09</td></tr>
    <tr style="background:#eee"><td>Description and Text Goes here</td><td>20.09</td><td>20.09</td><td>20.09</td></tr>
    <tr style="background:var(--charcoal)"><td style="color:#fff;font-weight:700">Description and Text Goes here</td><td style="color:#fff">20.09</td><td style="color:#fff">20.09</td><td style="color:#fff">20.09</td></tr>
    <tr style="background:#d8d8d8"><td>Description and Text Goes here</td><td>60.555</td><td>60.555</td><td>60.555</td></tr>
    <tr style="background:#eee"><td>Description and Text Goes here</td><td>85040</td><td>85040</td><td>85040</td></tr>
    <tr style="background:#d8d8d8"><td>Description and Text Goes here</td><td>85.09</td><td>85.09</td><td>85.09</td></tr>
    <tr><td style="background:#000;color:#fff;font-weight:700;font-size:3px">TOTAL VALUE</td><td style="background:var(--charcoal);color:#fff;font-weight:700">$ 2000,900</td><td style="background:var(--brown);color:#fff;font-weight:700">$ 800,900</td><td style="background:var(--gold);color:#fff;font-weight:700">$ 1000,900</td></tr>
  </table>
  <div class="foot"><span>www.quillbrook.biz</span><i>13</i></div>
</section>

<!-- 14 annual table -->
<section class="slide c2 r4">
  <svg class="flag" viewBox="0 0 14 7"><polygon points="0,0 13,0 13,7 6,3" fill="var(--gold)"/><polygon points="0,0 6,3 3,4" fill="var(--charcoal)"/></svg>
  <div class="title">Annual <b>Table</b></div>
  <svg class="abs" style="left:18px;top:34px" width="40" height="22" fill="none" stroke="#222" stroke-width=".8"><circle cx="10" cy="11" r="10"/><path d="M6 7l8 8M14 7l-8 8"/><circle cx="30" cy="11" r="10"/><path d="M30 5v12M28 6h4"/></svg>
  <div class="abs" style="left:79px;top:35px;font-size:4px;font-weight:700">Company budget files 2021</div>
  <p class="abs t" style="left:79px;top:42px;width:132px;font-size:2.4px;font-style:italic">Lorem ipsum dolor sit amet ligula suspendisse nulla pretium rhoncus tempor fermentum enim integer ad vestibulum volutpat nisl rhoncus turpis est vel elit congue wisi enim nunc ultricies sit magna tincidunt.</p>
  <table class="tbl abs" style="left:12px;top:62px;width:200px">
    <tr style="border-bottom:.5px solid #999"><td style="text-align:left;color:var(--gold);font-weight:700;font-size:2.8px">Nisl rhoncus turpis est</td><td style="color:var(--gold);font-weight:700">2014</td><td style="color:var(--gold);font-weight:700">2015</td><td style="color:var(--gold);font-weight:700">2016</td><td style="color:var(--gold);font-weight:700">2017</td></tr>
    <tr style="border-bottom:.3px solid #ddd;height:8.5px"><td style="text-align:left">Praesent condimentum arcu</td><td>4.456</td><td>4.456</td><td>4.456</td><td>4.456</td></tr>
    <tr style="border-bottom:.3px solid #ddd;height:8.5px"><td style="text-align:left">Praesent condimentum arcu</td><td>5.345</td><td>5.345</td><td>5.345</td><td>5.345</td></tr>
    <tr style="border-bottom:.3px solid #ddd;height:8.5px"><td style="text-align:left">Praesent condimentum arcu</td><td>6.567</td><td>6.567</td><td>6.567</td><td>6.567</td></tr>
    <tr style="border-bottom:.3px solid #ddd;height:8.5px"><td style="text-align:left">Praesent condimentum arcu</td><td>7.678</td><td>7.678</td><td>7.678</td><td>7.678</td></tr>
    <tr style="border-bottom:.3px solid #999;height:8.5px"><td style="text-align:left">Praesent condimentum arcu</td><td>8.789</td><td>8.789</td><td>8.789</td><td>8.789</td></tr>
    <tr><td style="text-align:left;color:#333;font-weight:500">CHANGE 20%</td><td></td><td></td><td></td><td></td></tr>
  </table>
  <div class="abs" style="left:215px;top:34px;width:62px;font-size:3px;color:#fff">
    <div style="background:var(--gold);height:13px;padding:4.5px 5px">STATS MANAGER</div>
    <div style="background:var(--charcoal);height:22px;margin-top:.7px;padding:5px 8px;line-height:1.5">THIS YEAR<br>17,250</div>
    <div style="background:var(--charcoal);height:22px;margin-top:.7px;padding:5px 8px;line-height:1.5">THIS MONTH<br>3,000</div>
    <div style="background:var(--charcoal);height:22px;margin-top:.7px;padding:5px 8px;line-height:1.5">THIS WEEK<br>450</div>
    <div style="background:var(--charcoal);height:22px;margin-top:.7px;padding:5px 8px;line-height:1.5">TODAY<br>225</div>
  </div>
  <div class="foot"><span>www.quillbrook.biz</span><i>14</i></div>
</section>

<!-- 15 clients -->
<section class="slide c3 r4">
  <svg class="flag" viewBox="0 0 14 7"><polygon points="0,0 13,0 13,7 6,3" fill="var(--gold)"/><polygon points="0,0 6,3 3,4" fill="var(--charcoal)"/></svg>
  <div class="title">Our <b>Clients</b></div>
  <div class="sub">Insert Your Creative Idea</div>
  <table class="tbl abs" style="left:15px;top:40px;width:247px;border:.4px solid #ccc">
    <tr><th style="background:var(--charcoal);color:#fff;width:24px;height:6px">NO</th><th style="background:var(--charcoal);color:#fff">CATEGORY 1</th><th style="background:var(--brown);color:#fff">CATEGORY 2</th><th style="background:var(--gold);color:#fff">CATEGORY 3</th></tr>
    <tr style="height:21px;border-bottom:.4px solid #ccc"><td>1</td><td class="client">Fenstra</td><td class="client">Robolt</td><td class="client">Sorvane</td></tr>
    <tr style="height:21px;border-bottom:.4px solid #ccc"><td>2</td><td class="client">Kernix</td><td class="client">Orbis</td><td class="client">Mivero</td></tr>
    <tr style="height:21px"><td>3</td><td class="client">Pomel</td><td class="client">Duskberry</td><td class="client">Ovano</td></tr>
  </table>
  <div class="abs" style="left:17px;top:122px;font-size:2.8px;font-weight:700">Insert Your Creative Idea</div>
  <p class="abs t" style="left:17px;top:127px;width:245px;font-size:2.4px">Lorem ipsum dolor sit amet consectetur adipiscing elit nulla imperdiet volutpat dui at fermentum aliquam erat volutpat aenean lacinia lacus aliquet ante mollis sollicitudin tempor tortor aliquam.</p>
  <div class="foot"><span>www.quillbrook.biz</span><i>15</i></div>
</section>

<!-- 16 team -->
<section class="slide c4 r4">
  <svg class="flag" viewBox="0 0 14 7"><polygon points="0,0 13,0 13,7 6,3" fill="var(--gold)"/><polygon points="0,0 6,3 3,4" fill="var(--charcoal)"/></svg>
  <div class="title">Meet Awesome <b>Team</b></div>
  <div class="sub">Insert Your Creative Idea</div>
  <div class="photo" role="img" aria-label="Portrait of team member, designer" style="left:28px;top:48px;width:61px;height:61px;border-radius:50%;background:radial-gradient(circle at 50% 40%,#d8c7b5,#8b7f74 70%)"></div>
  <div class="photo" role="img" aria-label="Portrait of team member, designer" style="left:110px;top:48px;width:61px;height:61px;border-radius:50%;background:radial-gradient(circle at 50% 40%,#c9ccd0,#6f7378 70%)"></div>
  <div class="photo" role="img" aria-label="Portrait of team member, designer" style="left:189px;top:48px;width:61px;height:61px;border-radius:50%;background:radial-gradient(circle at 50% 40%,#4a4a4c,#1c1c1e 70%)"></div>
  <div class="abs center" style="left:18px;top:117px;width:80px;font-size:4.3px">MARA DELL<div class="t" style="font-size:2.5px">DESIGNER</div></div>
  <div class="abs center" style="left:100px;top:117px;width:80px;font-size:4.3px">ADEN KOLE<div class="t" style="font-size:2.5px">DESIGNER</div></div>
  <div class="abs center" style="left:180px;top:117px;width:80px;font-size:4.3px">ARIN GROVE<div class="t" style="font-size:2.5px">DESIGNER</div></div>
  <div class="foot"><span>www.quillbrook.biz</span><i>16</i></div>
</section>

<!-- 17 ceo -->
<section class="slide c1 r5">
  <div class="photo" role="img" aria-label="Businessman in white shirt and red tie holding a jacket and bag" style="left:0;top:0;width:140px;height:156px;clip-path:polygon(0 0,140px 0,75px 156px,0 156px);background:linear-gradient(180deg,#dfe3e6,#aeb4b9 60%,#4b4f55)"></div>
  <div class="abs" style="left:8px;top:137px;font-size:5px;font-weight:700;color:#fff">Meet <span class="gold">CEO</span></div>
  <svg class="flag" style="left:148px" viewBox="0 0 14 7"><polygon points="0,0 13,0 13,7 6,3" fill="var(--gold)"/><polygon points="0,0 6,3 3,4" fill="var(--charcoal)"/></svg>
  <div class="abs" style="left:147px;top:17px;font-size:9.5px;font-weight:700">Mara <span class="gold">Dell</span></div>
  <div class="abs" style="left:147px;top:30px;width:68px;height:.4px;background:#999"></div>
  <div class="abs t" style="left:147px;top:33px;letter-spacing:1px">ABOUT CEO</div>
  <p class="abs t" style="left:147px;top:40px;width:117px;font-size:2.5px;text-align:justify">Lorem ipsum dolor sit amet consectetur adipiscing elit nulla imperdiet volutpat dui at fermentum aliquam erat volutpat aenean lacinia lacus aliquet ante mollis sollicitudin tempor tortor aliquam nulla facilisi nam auctor metus vitae quam gravida ac vehicula elit mollis nunc elementum fringilla nisl a ornare arcu condimentum a nulla euismod congue arcu quis feugiat phasellus porttitor felis mauris sed suscipit quam egestas nec.</p>
  <div class="abs" style="left:147px;top:76px;display:flex;gap:1.5px"><span style="width:3px;height:3px;background:var(--gold)"></span><span style="width:3px;height:3px;background:var(--gold)"></span><span style="width:3px;height:3px;background:var(--gold)"></span></div>
  <svg class="abs" style="left:150px;top:84px" width="120" height="46" font-size="2.2" text-anchor="middle" fill="#888">
    <g transform="translate(12,14)"><circle r="8" fill="none" stroke="#e8e8e8" stroke-width="3"/><circle r="8" fill="none" stroke="var(--gold)" stroke-width="3" stroke-dasharray="15 50" transform="rotate(-90)"/><circle r="5" fill="#fff" stroke="#333" stroke-width=".3"/><text y="22" fill="#333">CREATIVE</text></g>
    <g transform="translate(54,14)"><circle r="8" fill="none" stroke="#e8e8e8" stroke-width="3"/><circle r="8" fill="none" stroke="var(--gold)" stroke-width="3" stroke-dasharray="26 50" transform="rotate(-90)"/><circle r="5" fill="#fff" stroke="#333" stroke-width=".3"/><text y="22" fill="#333">ENJOYING</text></g>
    <g transform="translate(96,14)"><circle r="8" fill="none" stroke="#e8e8e8" stroke-width="3"/><circle r="8" fill="none" stroke="var(--gold)" stroke-width="3" stroke-dasharray="38 50" transform="rotate(-90)"/><circle r="5" fill="#fff" stroke="#333" stroke-width=".3"/><text y="22" fill="#333">PRO</text></g>
    <text x="12" y="30">■ 1st Qtr ■ 2nd Qtr</text><text x="54" y="30">■ 1st Qtr ■ 2nd Qtr</text><text x="96" y="30">■ 1st Qtr ■ 2nd Qtr</text>
  </svg>
  <div class="foot"><span>www.quillbrook.biz</span><i>17</i></div>
</section>

<!-- 18 map chart -->
<section class="slide c2 r5">
  <svg class="flag" viewBox="0 0 14 7"><polygon points="0,0 13,0 13,7 6,3" fill="var(--gold)"/><polygon points="0,0 6,3 3,4" fill="var(--charcoal)"/></svg>
  <div class="title">Map Chart <b>Concept</b></div>
  <div class="photo" role="img" aria-label="Map of the United States" style="left:12px;top:36px;width:108px;height:55px;border-radius:10px 18px 14px 20px;background:#d4d4d4"></div>
  <svg class="abs" style="left:130px;top:38px" width="140" height="62" font-size="2.5" fill="#666">
    <g fill="none" stroke="#eee" stroke-width=".3"><path d="M10 2h125M10 8h125M10 14h125M10 20h125M10 26h125M10 32h125M10 38h125M10 44h125M10 50h125"/></g>
    <text x="0" y="3">100</text><text x="2" y="27">50</text><text x="4" y="51">10</text>
    <path d="M14 40 C30 30,45 45,60 38 S90 10,110 5 S125 40,130 48" fill="none" stroke="var(--gold)" stroke-width=".7"/>
    <path d="M14 45 C30 50,45 30,65 35 S95 50,110 40 S125 10,130 8" fill="none" stroke="var(--charcoal)" stroke-width=".7"/>
    <path d="M14 42 C40 44,60 42,80 30 S115 15,130 20" fill="none" stroke="#e5c46b" stroke-width=".7"/>
    <text x="10" y="58">2012</text><text x="25" y="58">2013</text><text x="40" y="58">2014</text><text x="55" y="58">2015</text><text x="70" y="58">2016</text><text x="85" y="58">2017</text><text x="100" y="58">2018</text><text x="115" y="58">2019</text><text x="128" y="58">2020</text>
  </svg>
  <div class="abs" style="left:14px;top:110px;font-size:4.3px;font-weight:700">Contrary to popular belief,</div>
  <p class="abs t" style="left:14px;top:117px;width:107px;font-size:2.3px;font-style:italic">"At vero eos et accusamus et iusto odio dignissimos ducimus blanditiis praesentium voluptatum deleniti atque corrupti quos dolores et quas molestias excepturi sint occaecati vasi architecto beatae vitae dicta sunt</p>
  <div class="abs" style="left:128px;top:115px;width:18px;height:18px;border-radius:50%;background:var(--charcoal)"></div>
  <svg class="abs" style="left:133px;top:119px" width="8" height="10"><path d="M4 .5 7.5 2v3.5C7.5 7.5 4 9.5 4 9.5S.5 7.5.5 5.5V2z" fill="none" stroke="#fff" stroke-width=".7"/></svg>
  <div class="abs" style="left:150px;top:117px;width:38px"><div style="font-size:2.8px;font-weight:700">Feature keyword</div><p class="t" style="font-size:2.1px">"All the Lorem" ipsum generators on the internet tend to repeat predefined</p></div>
  <div class="abs" style="left:200px;top:115px;width:18px;height:18px;border-radius:50%;background:var(--gold)"></div>
  <div class="abs" style="left:222px;top:117px;width:40px"><div style="font-size:2.8px;font-weight:700">Feature keyword</div><p class="t" style="font-size:2.1px">"All the Lorem" ipsum generators on the internet tend to repeat predefined</p></div>
  <div class="foot"><span>www.quillbrook.biz</span><i>18</i></div>
</section>

<!-- 19 world maps -->
<section class="slide c3 r5">
  <svg class="flag" viewBox="0 0 14 7"><polygon points="0,0 13,0 13,7 6,3" fill="var(--gold)"/><polygon points="0,0 6,3 3,4" fill="var(--charcoal)"/></svg>
  <div class="title">World <b>Maps</b></div>
  <div class="photo" role="img" aria-label="World map with North America highlighted in dark and China in gold" style="left:25px;top:45px;width:185px;height:90px;border-radius:30px 40px 30px 40px;background:radial-gradient(circle at 25% 35%,#2a2f35 0 9px,transparent 10px),radial-gradient(circle at 75% 35%,#c4922f 0 8px,transparent 9px),#d6d6d6"></div>
  <svg class="abs" style="left:213px;top:37px" width="14" height="14" fill="none" stroke="#333" stroke-width=".6"><circle cx="7" cy="6" r="5"/><path d="M7 11v3M5 14h4"/></svg>
  <div class="abs center" style="left:190px;top:53px;width:60px;font-size:4.2px;font-weight:700">we are <span class="gold">growing</span></div>
  <p class="abs center t" style="left:195px;top:60px;width:50px;font-size:2.4px">lorem ipsum dolor sit amet, consectetur adipiscing elit. maecenas</p>
  <svg class="abs" style="left:213px;top:84px" width="14" height="14" fill="none" stroke="#333" stroke-width=".6"><circle cx="7" cy="6" r="5"/><path d="M2 6h10M7 1v10"/></svg>
  <div class="abs center" style="left:190px;top:100px;width:60px;font-size:4.2px;font-weight:700"><span class="gold">join</span> the crew</div>
  <p class="abs center t" style="left:195px;top:107px;width:50px;font-size:2.4px">lorem ipsum dolor sit amet, consectetur adipiscing elit. maecenas</p>
  <div class="foot"><span>www.quillbrook.biz</span><i>19</i></div>
</section>

<!-- 20 graph chart -->
<section class="slide c4 r5">
  <svg class="flag" viewBox="0 0 14 7"><polygon points="0,0 13,0 13,7 6,3" fill="var(--gold)"/><polygon points="0,0 6,3 3,4" fill="var(--charcoal)"/></svg>
  <div class="title">Graph <b>Chart</b></div>
  <svg class="abs" style="left:12px;top:36px" width="160" height="98" font-size="2.8" fill="#555">
    <g fill="none" stroke="#e5e5e5" stroke-width=".3"><path d="M10 3h148M10 16h148M10 29h148M10 42h148M10 55h148M10 68h148M10 81h148"/></g>
    <text x="2" y="4">6</text><text x="2" y="17">5</text><text x="2" y="30">4</text><text x="2" y="43">3</text><text x="2" y="56">2</text><text x="2" y="69">1</text><text x="2" y="82">0</text>
    <rect x="26" y="25" width="6" height="56" fill="#1f262e"/><rect x="33" y="48" width="6" height="33" fill="#7a5a45"/><rect x="40" y="22" width="6" height="59" fill="#c4922f"/>
    <rect x="71" y="16" width="6" height="65" fill="#1f262e"/><rect x="78" y="35" width="6" height="46" fill="#7a5a45"/><rect x="85" y="42" width="6" height="39" fill="#c4922f"/>
    <rect x="117" y="50" width="6" height="31" fill="#1f262e"/><rect x="124" y="24" width="6" height="57" fill="#7a5a45"/><rect x="131" y="45" width="6" height="36" fill="#c4922f"/>
    <text x="28" y="89">category 1</text><text x="73" y="89">category 2</text><text x="118" y="89">category 3</text>
  </svg>
  <div class="abs" style="left:171px;top:10px;width:96px;font-size:4.5px;line-height:1.2;color:#333">• Lorem ipsum dolor sit amet, consectetuer adipiscing elit. Maecenas porttitor congue massa.</div>
  <div class="abs" style="left:171px;top:43px;display:flex;flex-direction:column;gap:13px">
    <div style="display:flex;gap:5px"><span style="width:13px;height:13px;border-radius:50%;background:var(--charcoal);flex:none"></span><div><div style="font-size:3.6px;font-weight:700">option one</div><p class="t" style="font-size:2.3px">Lorem ipsum dolor sit amet, consectetuer adipiscing elit.</p></div></div>
    <div style="display:flex;gap:5px"><span style="width:13px;height:13px;border-radius:50%;background:var(--brown);flex:none"></span><div><div style="font-size:3.6px;font-weight:700">option two</div><p class="t" style="font-size:2.3px">Lorem ipsum dolor sit amet, consectetuer adipiscing elit.</p></div></div>
    <div style="display:flex;gap:5px"><span style="width:13px;height:13px;border-radius:50%;background:var(--gold);flex:none"></span><div><div style="font-size:3.6px;font-weight:700">option three</div><p class="t" style="font-size:2.3px">Lorem ipsum dolor sit amet, consectetuer adipiscing elit.</p></div></div>
  </div>
  <div class="foot"><span>www.quillbrook.biz</span><i>20</i></div>
</section>

<!-- 21 overview chart -->
<section class="slide c1 r6">
  <svg class="flag" viewBox="0 0 14 7"><polygon points="0,0 13,0 13,7 6,3" fill="var(--gold)"/><polygon points="0,0 6,3 3,4" fill="var(--charcoal)"/></svg>
  <div class="abs" style="left:12px;top:19px;font-size:9px;font-weight:700">Overview <span class="gold">Chart</span></div>
  <p class="abs t" style="left:116px;top:14px;width:110px;font-size:3px;font-style:italic;color:#444">Lorem ipsum dolor sit amet, consectetuer adipiscing elit. Maecenas porttitor congue massa.</p>
  <svg class="abs" style="left:8px;top:48px" width="262" height="62" font-size="2.6" fill="#666">
    <text x="40" y="3" font-size="4">Sales</text><text x="126" y="3" font-size="4">Demand</text><text x="210" y="3" font-size="4">Statistic</text>
    <g fill="none" stroke="#ddd" stroke-width=".3"><path d="M10 10v45h78M102 10v45h78M190 10v45h70"/></g>
    <path d="M14 55V34L40 36 52 44 80 26V55z" fill="#c4922f"/>
    <path d="M14 15 40 17 52 28 80 14 80 26 52 44 40 36 14 34z" fill="#1f262e"/>
    <g fill="#1f262e"><rect x="108" y="22" width="4" height="33"/><rect x="124" y="30" width="4" height="25"/><rect x="140" y="25" width="4" height="30"/><rect x="156" y="20" width="4" height="35"/></g>
    <g fill="#c4922f"><rect x="113" y="30" width="4" height="25"/><rect x="129" y="15" width="4" height="40"/><rect x="145" y="42" width="4" height="13"/><rect x="161" y="33" width="4" height="22"/></g>
    <path d="M198 22C210 30,215 40,225 32S240 18,255 15" fill="none" stroke="#1f262e" stroke-width=".6"/>
    <path d="M198 35C212 34,228 28,255 16" fill="none" stroke="#c4922f" stroke-width=".6"/>
    <text x="12" y="60">may</text><text x="36" y="60">jun</text><text x="60" y="60">jul</text><text x="80" y="60">aug</text>
    <text x="106" y="60">may</text><text x="130" y="60">jun</text><text x="152" y="60">jul</text><text x="172" y="60">aug</text>
    <text x="194" y="60">may</text><text x="218" y="60">jun</text><text x="238" y="60">jul</text><text x="252" y="60">aug</text>
  </svg>
  <svg class="abs" style="left:28px;top:124px" width="14" height="10" fill="none" stroke="#333" stroke-width=".6"><path d="M1 9V6M4 9V4M7 9V2M10 9V5M0 9.5h13"/></svg>
  <p class="abs t" style="left:59px;top:125px;width:190px;font-size:2.4px;color:#555">It was popularized in the 1960s with the release of sheets containing Lorem Ipsum passages, and more recently with desktop publishing software including versions of Lorem Ipsum.</p>
  <div class="foot"><span>www.quillbrook.biz</span><i>21</i></div>
</section>

<!-- 22 single list -->
<section class="slide c2 r6">
  <svg class="flag" viewBox="0 0 14 7"><polygon points="0,0 13,0 13,7 6,3" fill="var(--gold)"/><polygon points="0,0 6,3 3,4" fill="var(--charcoal)"/></svg>
  <div class="title">Single <b>List</b></div>
  <p class="abs" style="left:25px;top:34px;width:225px;font-size:3.4px;line-height:1.4;color:#444"><b class="gold">Contrary to popular belief,</b> Lorem Ipsum is not simply random text. It has roots in a piece of classical Latin literature from 45 BC.</p>
  <div class="abs" style="left:25px;top:53px;width:225px;height:.5px;background:#555"></div>
  <ul class="abs t" style="left:37px;top:67px;width:200px;list-style:none;font-size:2.5px;display:flex;flex-direction:column;gap:7px">
    <li>◉&nbsp; Quisque libero purus, bibendum nec quam sit amet, porta interdum ex. Aliquam erat volutpat. Quisque commodo lacus sed lectus condimentum cursus.</li>
    <li>◉&nbsp; Praesent a diam neque. Aenean ultricies eu orci id euismod. Integer eleifend, lacus quis tincidunt posuere, nisl neque sodales justo, quis suscipit libero odio ut quam.</li>
    <li>◉&nbsp; Nam auctor, leo a volutpat rhoncus, erat arcu dignissim velit, in aliquet erat metus quis tellus. Vestibulum nec lobortis augue, at interdum nisl.</li>
  </ul>
  <p class="abs t" style="left:29px;top:118px;width:220px;font-size:2.7px;color:#555;line-height:2">Cras laoreet mauris eget pharetra auctor. Donec lacinia est id euismod eleifend. Quisque condimentum varius ullamcorper.<br>Nunc quam libero, feugiat ut ante eu, ultrices efficitur erat.</p>
  <div class="foot"><span>www.quillbrook.biz</span><i>22</i></div>
</section>

<!-- 23 two column -->
<section class="slide c3 r6">
  <svg class="flag" viewBox="0 0 14 7"><polygon points="0,0 13,0 13,7 6,3" fill="var(--gold)"/><polygon points="0,0 6,3 3,4" fill="var(--charcoal)"/></svg>
  <div class="title">Two Column <b>Text</b></div>
  <p class="abs" style="left:27px;top:33px;width:225px;font-size:2.7px;line-height:1.4;color:#555"><b class="gold">Contrary to popular belief,</b> Lorem Ipsum is not simply random text. It has roots in a piece of classical Latin literature from 45 BC. Cras laoreet mauris eget pharetra auctor. Donec lacinia est id euismod eleifend. Quisque condimentum varius ullamcorper.</p>
  <div class="abs" style="left:27px;top:52px;width:225px;height:.4px;background:#777"></div>
  <p class="abs t" style="left:28px;top:57px;width:108px;font-size:2.3px;text-align:justify">Lorem ipsum dolor sit amet, consectetur adipiscing elit. Etiam et libero quis risus finibus sollicitudin nec vel nibh. Praesent condimentum arcu sed congue bibendum. Nulla facilisi. Curabitur pretium ante tincidunt rhoncus ante sed. Nam auctor metus vitae quam gravida, ac vehicula elit mollis. Nunc elementum fringilla nisl, a ornare arcu condimentum a. Nulla euismod congue arcu quis feugiat. Phasellus porttitor felis mauris, sed suscipit quam egestas nec. Aliquam erat volutpat. Quisque commodo lacus sed lectus condimentum cursus. Praesent a diam neque. Aenean ultricies eu orci id euismod. Integer eleifend, lacus quis tincidunt posuere, nisl neque sodales justo, quis suscipit libero odio ut quam. Mauris dapibus urna ut ex commodo, non elementum libero feugiat. Quisque libero purus, bibendum nec quam sit amet, porta interdum ex. Aliquam erat volutpat. Quisque commodo lacus sed lectus condimentum cursus. Praesent a diam neque, integer eleifend lacus quis tincidunt posuere, nisl neque sodales justo quis suscipit libero odio ut quam.</p>
  <p class="abs t" style="left:144px;top:57px;width:108px;font-size:2.3px;text-align:justify">volutpat rhoncus, erat arcu dignissim velit, in aliquet erat metus quis tellus. Vestibulum nec lobortis augue, at interdum nisl. Maecenas venenatis faucibus lectus, quis iaculis orci tincidunt auctor. Nunc quam libero, feugiat ut ante eu, ultrices efficitur erat. Duis sit amet dui convallis, pretium libero eu, mollis tortor. Morbi rutrum, diam vel congue suscipit, lectus velit congue magna, quis fermentum justo arcu non purus. Fusce lorem ipsum dolor sit amet, consectetur adipiscing elit. Aenean id lectus vel erat luctus viverra sit amet in diam. Phasellus ut augue vitae orci lobortis fringilla. Integer quis nisl nisi. Vivamus sollicitudin ac nisl non lobortis. Aenean cursus, nisl volutpat vulputate commodo, ex lacus maximus dolor, et hendrerit odio velit eget augue. Integer vel lacinia lacus, ut auctor ante.</p>
  <div class="foot"><span>www.quillbrook.biz</span><i>23</i></div>
</section>

<!-- 24 thank you -->
<section class="slide c4 r6">
  <svg class="abs" style="left:0;top:0" width="277" height="156"><polygon points="188,0 277,0 277,156 80,156" fill="var(--charcoal)"/></svg>
  <div class="photo" role="img" aria-label="Smiling woman wearing a headset at a help desk" style="left:28px;top:27px;width:222px;height:101px;background:linear-gradient(90deg,#2a3038,#4a5058 55%,#6f747a)"></div>
  <svg class="abs" style="left:225px;top:103px" width="25" height="25"><polygon points="25,0 25,25 0,25" fill="var(--gold)"/></svg>
  <div class="abs" style="left:134px;top:52px"><span class="mark"></span></div>
  <div class="abs center" style="left:80px;top:66px;width:115px;font-size:9px;font-weight:700;color:#fff">Thank <span class="gold">You</span></div>
  <p class="abs center" style="left:80px;top:78px;width:115px;font-size:3.5px;line-height:1.4;color:#ddd">Lorem Ipsum is simply dummy text of the printing and typesetting industry.</p>
  <div class="abs" style="left:34px;top:99px;color:#fff;font-size:2.2px;line-height:1.35">
    <div style="font-size:3px;font-weight:700">KENDALL MOSS</div>
    <div class="gold" style="font-weight:400">Director of Marketing and Public Sales</div>
    <div>kendall.moss@quillbrook.biz</div><div>(800) 555-0146 x571</div><div>Cell: +12 555 01 98 33</div>
  </div>
  <div class="abs" style="left:28px;top:139px;display:flex;gap:1.5px"><span style="width:4.5px;height:4.5px;border:.4px solid var(--gold)"></span><span style="width:4.5px;height:4.5px;border:.4px solid var(--gold)"></span><span style="width:4.5px;height:4.5px;border:.4px solid var(--gold)"></span><span style="width:4.5px;height:4.5px;border:.4px solid var(--gold)"></span></div>
</section>

</div>
</body>
</html>
```